Promotional business a5 Notepad design

I am looking for a custom a5 notepad design as a promotional item to give away to customers etc.
Attached will be a desk planner we had designed feel free to use as a reference.
We want the notepad to have lines running horizontal not squares like the desk planner example.

Industry/Entity Type

Hydraulic / industrial

Colors

Designer to choose colors to be used in the design.

```html
<!DOCTYPE html>
<html lang="en">
<head>
<meta charset="utf-8">
<title>Keystone Hose and Couplings – A5 Notepad</title>
<link href="https://fonts.googleapis.com/css2?family=Poppins:wght@400;600&display=swap" rel="stylesheet">
<style>
  :root {
    --brand-blue: #1b2fbf;
    --ink: #111111;
    --text-grey: #4a4a4a;
    --paper: #ffffff;
    --backdrop: #e6e6e6;
    --rule: #1a1a1a;
  }
  * { box-sizing: border-box; margin: 0; padding: 0; }
  html, body {
    width: 973px;
    height: 1200px;
    overflow: hidden;
    background: var(--backdrop);
    font-family: "Poppins", sans-serif;
  }
  .notepad {
    position: absolute;
    left: 62px;
    top: 0;
    width: 848px;
    height: 1200px;
    background: var(--paper);
    overflow: hidden;
  }
  .brand {
    position: absolute;
    left: 68px;
    top: 92px;
    display: flex;
    align-items: center;
    gap: 12px;
  }
  .brand-mark {
    width: 40px;
    height: 40px;
    border-radius: 50%;
    background: var(--brand-blue);
  }
  .brand-name {
    font-weight: 600;
    font-size: 21px;
    color: var(--brand-blue);
    letter-spacing: 0.2px;
  }
  .contact {
    position: absolute;
    left: 564px;
    top: 63px;
    font-size: 14px;
    line-height: 18px;
    color: var(--text-grey);
  }
  .contact-address { margin-bottom: 8px; }
  .contact-row {
    display: flex;
    align-items: center;
    gap: 9px;
    height: 18px;
  }
  .contact-row svg { width: 13px; height: 13px; flex: none; }
  .writing-lines {
    position: absolute;
    left: 70px;
    top: 0;
    width: 710px;
    height: 1200px;
  }
  .writing-lines span {
    position: absolute;
    left: 0;
    width: 100%;
    height: 1.5px;
    background: var(--rule);
  }
  .footer-band {
    position: absolute;
    left: 0;
    bottom: 0;
    width: 848px;
    height: 46px;
  }
  .footer-web {
    position: absolute;
    left: 597px;
    bottom: 10px;
    font-size: 16px;
    color: #ffffff;
    letter-spacing: 0.3px;
  }
</style>
</head>
<body>
  <main class="notepad">
    <header>
      <div class="brand">
        <span class="brand-mark"></span>
        <span class="brand-name">Keystone Hose and Couplings</span>
      </div>
      <address class="contact" style="font-style:normal">
        <div class="contact-address">4120 Larkspur Avenue<br>Fairbanks, Alaska 99701</div>
        <div class="contact-row">
          <svg viewBox="0 0 24 24" aria-hidden="true"><path fill="#1b2fbf" d="M6.6 10.8a15.1 15.1 0 0 0 6.6 6.6l2.2-2.2c.3-.3.7-.4 1-.2 1.1.4 2.3.6 3.6.6.6 0 1 .4 1 1V20c0 .6-.4 1-1 1A17 17 0 0 1 3 4c0-.6.4-1 1-1h3.5c.6 0 1 .4 1 1 0 1.3.2 2.5.6 3.6.1.3 0 .7-.2 1z"/></svg>
          <span>555-214-7830</span>
        </div>
        <div class="contact-row">
          <svg viewBox="0 0 24 24" aria-hidden="true"><rect x="2" y="5" width="20" height="14" fill="#1b2fbf"/><path d="M2 5l10 8 10-8" fill="none" stroke="#fff" stroke-width="2"/></svg>
          <span>name@keystonehose.com</span>
        </div>
      </address>
    </header>

    <div class="writing-lines" aria-hidden="true">
      <span style="top:221px"></span>
      <span style="top:284px"></span>
      <span style="top:348px"></span>
      <span style="top:411px"></span>
      <span style="top:474px"></span>
      <span style="top:537px"></span>
      <span style="top:600px"></span>
      <span style="top:663px"></span>
      <span style="top:726px"></span>
      <span style="top:789px"></span>
      <span style="top:852px"></span>
      <span style="top:916px"></span>
      <span style="top:978px"></span>
      <span style="top:1040px"></span>
    </div>

    <footer>
      <svg class="footer-band" viewBox="0 0 848 46" aria-hidden="true">
        <polygon points="0,34 540,34 530,46 0,46" fill="#1b2fbf"/>
        <polygon points="571,0 848,0 848,46 528,46" fill="#000000"/>
      </svg>
      <div class="footer-web">www.keystonehose.com</div>
    </footer>
  </main>
</body>
</html>
```